BUSINESS CARD DESIGN

NAME- DALE VORSKIN
PHONE NUMER - 555- 714-9082
EMAIL- OFFICE@TRV-GROUNDMAKRZ.COM
BACK OF CARD- SPEACIALIZES IN LAND CLEARING, FORESTRY MUCLHING AND EXCAVATION

Contact Information for Business Card

NAME- DALE VORSKIN PHONE NUMER - 555- 714-9082 EMAIL- OFFICE@TRV-GROUNDMAKRZ.COM BACK OF CARD- SPEACIALIZES IN LAND CLEARING , MUCLHING AND EXCAVATION

```html
<!DOCTYPE html>
<html lang="en">
<head>
<meta charset="utf-8">
<title>Business Card Design</title>
<link rel="stylesheet" href="https://fonts.googleapis.com/css2?family=Orbitron:wght@600;700&family=Montserrat:wght@700&display=swap">
<style>
  :root {
    --page: #dcdcdc;
    --band: #e2e2e2;
    --divider: #d0d0d0;
    --card: #000000;
    --silver: #c9c9c9;
    --white: #e9e9e9;
    --green: #2fd61f;
  }
  * { margin: 0; padding: 0; box-sizing: border-box; }
  html, body { width: 1056px; height: 1200px; overflow: hidden; }
  body { background: var(--page); position: relative; }
  .presentation-band {
    position: absolute; left: 0; top: 0; width: 1056px; height: 359px;
    background: var(--band); border-bottom: 1px solid var(--divider);
  }
  .card {
    position: absolute; top: 54px; width: 442px; height: 253px;
    background: var(--card); overflow: hidden;
  }
  .card--front { left: 68px; }
  .card--back { left: 546px; }

  .brand { position: absolute; display: flex; flex-direction: column; align-items: center; }
  .brand__mark { border: 3px solid var(--silver); border-radius: 50%; }
  .brand__name {
    font-family: "Orbitron", sans-serif; font-weight: 700; color: var(--silver);
    letter-spacing: 0.5px; white-space: nowrap; margin-top: 8px;
  }
  .card--front .brand { left: 23px; width: 180px; top: 80px; }
  .card--front .brand__mark { width: 80px; height: 80px; }
  .card--front .brand__name { font-size: 10.5px; }
  .card--back .brand { left: 121px; width: 200px; top: 62px; }
  .card--back .brand__mark { width: 96px; height: 96px; }
  .card--back .brand__name { font-size: 12px; }

  .person { position: absolute; left: 266px; top: 60px; font-family: "Orbitron", sans-serif; font-weight: 700; }
  .person__name { font-size: 11px; color: var(--white); letter-spacing: 0.6px; }
  .person__role {
    display: inline-block; margin-top: 5px; font-size: 10px; color: var(--silver);
    letter-spacing: 0.6px; padding-bottom: 2px; border-bottom: 2px solid var(--green);
  }

  .contacts { position: absolute; left: 262px; top: 170px; list-style: none; }
  .contacts li {
    display: flex; align-items: center; gap: 8px; height: 17px;
    font-family: "Montserrat", sans-serif; font-weight: 700; font-size: 5.6px;
    color: var(--white); letter-spacing: 0.3px;
  }
  .contacts svg { width: 9px; height: 9px; flex: none; }

  .tagline {
    position: absolute; left: 0; width: 100%; top: 212px; text-align: center;
    font-family: "Orbitron", sans-serif; font-weight: 700; font-size: 8.2px;
    line-height: 9.5px; letter-spacing: 0.4px;
  }
  .tagline__lead { color: var(--white); }
  .tagline__rest { color: var(--silver); }
</style>
</head>
<body>
  <div class="presentation-band"></div>

  <section class="card card--front" aria-label="Card front">
    <div class="brand">
      <div class="brand__mark"></div>
      <div class="brand__name">TREVALLO GROUNDMAKRZ</div>
    </div>
    <div class="person">
      <div class="person__name">DALE VORSKIN</div>
      <div class="person__role">OWNER</div>
    </div>
    <ul class="contacts">
      <li>
        <svg viewBox="0 0 10 10" fill="none" stroke="var(--green)" stroke-width="1"><path d="M2 1.2 L3.6 1 L4.3 3 L3.3 3.8 Q4.2 5.8 6.2 6.7 L7 5.7 L9 6.4 L8.8 8 Q5 8.6 1.4 5 Q1 3 2 1.2Z"/></svg>
        +555- 714-9082
      </li>
      <li>
        <svg viewBox="0 0 10 10" fill="none" stroke="var(--green)" stroke-width="1"><rect x="0.6" y="2" width="8.8" height="6.2"/><circle cx="3.2" cy="4.4" r="0.9" fill="var(--green)"/><path d="M5.5 4h2.6M5.5 5.6h2.6M2 6.8h2.4"/></svg>
        OFFICE@TRV-GROUNDMAKRZ.COM
      </li>
      <li>
        <svg viewBox="0 0 10 10" fill="none" stroke="var(--green)" stroke-width="1"><circle cx="5" cy="5" r="4"/><ellipse cx="5" cy="5" rx="1.8" ry="4"/><path d="M1 5h8M1.7 3h6.6M1.7 7h6.6"/></svg>
        WWW.TRV-GROUNDMAKRZ.COM
      </li>
    </ul>
  </section>

  <section class="card card--back" aria-label="Card back">
    <div class="brand">
      <div class="brand__mark"></div>
      <div class="brand__name">TREVALLO GROUNDMAKRZ</div>
    </div>
    <p class="tagline">
      <span class="tagline__lead">SPEACIALIZES IN LAND CLEARING</span><br>
      <span class="tagline__rest">MUCLHING AND EXCAVATION</span>
    </p>
  </section>
</body>
</html>
```